Business Card Design Project

Looking for a logo and business card for a Real State Business i will be opening. The name is not choosen yet , but will probably be RWT IMOVEIS.
I was thinking black and silver colors, but am open to nice ideas.
I did add a business card that i liked a lot, am looking for something like that, with logo in black or silver in a black card. The logo i was thinking in the letters RWT as i uploaded or something or little and cute buildings or a house...just ideas, can be any nice logo.
Updates

You guys can add other colors if you want, I like colors very "BRIGHT" and "open", like red, pink, strong colors. almost glow in the dark colors. lol

Designers,

I've increased more 88 dollars in the budget for 1st place cause I will want envelope designs... small and big sizes.

So 1st place is now U$248,00. 

No need to send the envelope designs right now... only the business cards designs.

Thank you.

Industry/Entity Type

Business

Requirements
Must have
• Marcela Tavares Rocha

www.RWTimoveis-exemplo.com.br

+554187316042

marcela@rwtimoveis-exemplo.com.br

```html
<!DOCTYPE html>
<html lang="pt-BR">
<head>
<meta charset="utf-8">
<title>RWT Imoveis – Business Cards</title>
<link rel="stylesheet" href="https://fonts.googleapis.com/css2?family=Josefin+Sans:wght@400;700&display=swap">
<style>
  :root {
    --bg: #3b3b3c;
    --card: #231f20;
    --skyline: #363436;
    --pink: #ec008c;
    --white: #ffffff;
  }
  * { box-sizing: border-box; margin: 0; padding: 0; }
  html, body { width: 1200px; height: 892px; overflow: hidden; }
  body {
    background: var(--bg);
    font-family: "Josefin Sans", "Century Gothic", sans-serif;
    position: relative;
  }
  .card {
    position: absolute;
    width: 620px;
    height: 360px;
    background: var(--card);
    overflow: hidden;
    box-shadow: 0 8px 24px rgba(0,0,0,0.45);
  }
  .card--front { left: 545px; top: 60px; }
  .card--back  { left: 40px;  top: 462px; }

  .skyline {
    position: absolute;
    left: 0; right: 0; bottom: 0;
    height: 130px;
    background: linear-gradient(to top, var(--skyline) 45%, rgba(54,52,54,0.35) 100%);
  }

  /* front */
  .brand {
    position: absolute;
    left: 165px; top: 48px;
    z-index: 1;
    white-space: nowrap;
  }
  .brand__name {
    color: var(--pink);
    font-weight: 700;
    font-size: 72px;
    line-height: 0.95;
    letter-spacing: 1px;
  }
  .brand__tagline {
    color: var(--pink);
    font-weight: 400;
    font-size: 34px;
    margin-top: 10px;
    margin-left: 2px;
  }

  /* back */
  .back__mark {
    position: absolute;
    left: 95px; top: 82px;
    color: var(--pink);
    font-weight: 700;
    font-size: 56px;
    line-height: 1;
    z-index: 1;
  }
  .contact {
    position: absolute;
    left: 262px; top: 78px;
    z-index: 1;
    white-space: nowrap;
  }
  .contact__name {
    color: var(--pink);
    font-weight: 700;
    font-size: 19px;
  }
  .contact__role {
    color: var(--white);
    font-size: 16px;
    margin-top: 6px;
  }
  .contact__list {
    list-style: none;
    margin-top: 28px;
    color: var(--white);
    font-size: 16px;
  }
  .contact__list li {
    display: flex;
    align-items: center;
    gap: 10px;
    height: 24px;
  }
  .contact__list .icon { width: 16px; height: 14px; flex: none; }
  .contact__list .web { font-size: 19px; margin-top: 6px; }
</style>
</head>
<body>

<section class="card card--front">
  <div class="brand">
    <div class="brand__name">RWT<br>IMOVEIS</div>
    <div class="brand__tagline">Real Estate Agent</div>
  </div>
  <div class="skyline" role="img" aria-label="City skyline silhouette along the bottom of the card"></div>
</section>

<section class="card card--back">
  <div class="back__mark">RWT</div>
  <div class="contact">
    <div class="contact__name">Marcela Tavares Rocha</div>
    <div class="contact__role">Real Estate Agent</div>
    <ul class="contact__list">
      <li>
        <svg class="icon" viewBox="0 0 16 14" aria-hidden="true">
          <path fill="#ec008c" d="M1 4c0-2 3-3 7-3s7 1 7 3v1h-3V3.5C11 3 9.5 2.8 8 2.8S5 3 4 3.5V5H1z"/>
          <rect x="3" y="6" width="10" height="7" rx="1" fill="#ec008c"/>
          <circle cx="8" cy="9.5" r="1.6" fill="#231f20"/>
        </svg>
        <span>+55 4187 316 042</span>
      </li>
      <li>
        <svg class="icon" viewBox="0 0 16 12" aria-hidden="true">
          <rect x="0" y="0" width="16" height="12" rx="1" fill="#ec008c"/>
          <path d="M1 1l7 6 7-6" fill="none" stroke="#231f20" stroke-width="1.4"/>
        </svg>
        <span>marcela@rwtimoveis-exemplo.com.br</span>
      </li>
      <li class="web"><span>www.RWTimoveis-exemplo.com.br</span></li>
    </ul>
  </div>
  <div class="skyline" role="img" aria-label="City skyline silhouette along the bottom of the card"></div>
</section>

</body>
</html>
```